Business Card for new Architectural Firm

I intend to practice in a rural mountain community in upstate NY, focusing on residential and light commercial projects, including second home / vacation properties. I wish to convey a feeling of rural outdoorsy modernity.

Color is important - bold and urbane. Secondary or tertiary colors preferred.

Font is important, idiosyncratic is ok

Optionally, I may choose to use the name Brambleford Studio. If used as part of your design, all of the Must Haves are still required.

Images uploaded are logos I like

Industry/Entity Type

Residential

Contact Information for Business Card

Calvin Worthaven
Architect (This word should stand alone or be associated with my name - not license number)
NY License No. 052816
calvin@designbycw.com
607 385 2194

Font styles to use
Sans Serif
Decorative

Requirements
Must have
• Whatever files I need to best utilize your design
• PDF
• JPG
• EPS
• Vectorwhatsit
Nice to have
• Logo or element that can be incorporated into other print material.
• Could be a font based card
Should not have
• no clip art
• No templates
• no floor plans
• no building photographs

```html
<!DOCTYPE html>
<html lang="en">
<head>
<meta charset="utf-8">
<title>Calvin Worthaven Architect – Business Cards</title>
<link rel="stylesheet" href="https://fonts.googleapis.com/css2?family=Montserrat:wght@300;600&family=Oswald:wght@600&display=swap">
<style>
  :root {
    --page: #e4e4e4;
    --card-light: #f4f4f2;
    --card-dark: #8a8a8a;
    --green: #7cc242;
    --rule: #8f8f8f;
    --ink-grey: #8c8c8c;
    --ink-dark: #6e6e6e;
    --ink-soft: #ececec;
    --white: #ffffff;
  }
  * { box-sizing: border-box; margin: 0; padding: 0; }
  html, body {
    width: 1200px;
    height: 1000px;
    overflow: hidden;
    background: var(--page);
  }
  .sheet {
    width: 1200px;
    height: 1000px;
    display: flex;
    flex-direction: column;
    align-items: center;
    justify-content: center;
    gap: 44px;
  }
  .card {
    position: relative;
    width: 760px;
    height: 434px;
    box-shadow: 0 6px 18px rgba(0,0,0,0.18);
  }
  .card--light { background: var(--card-light); }
  .card--dark { background: var(--card-dark); }

  .rule {
    position: absolute;
    height: 4px;
    background: var(--rule);
  }
  .rule--top { left: 150px; right: 60px; top: 46px; }
  .rule--bottom { left: 150px; right: 60px; top: 262px; }

  .identity {
    position: absolute;
    right: 60px;
    text-align: right;
  }
  .card--light .identity { top: 66px; }
  .card--dark .identity { top: 78px; }

  .identity__name {
    font-family: "Montserrat", sans-serif;
    font-weight: 600;
    font-size: 52px;
    line-height: 0.98;
    letter-spacing: 3px;
    text-transform: uppercase;
    color: var(--green);
  }
  .identity__title {
    font-family: "Oswald", sans-serif;
    font-weight: 600;
    font-size: 24px;
    letter-spacing: 1px;
    margin-top: 4px;
  }
  .card--light .identity__title { color: var(--ink-dark); }
  .card--dark .identity__title { color: var(--white); }

  .contact {
    position: absolute;
    right: 60px;
    list-style: none;
    text-align: right;
    font-family: "Montserrat", sans-serif;
    font-weight: 300;
    font-size: 19px;
    line-height: 1.75;
  }
  .card--light .contact { top: 284px; color: var(--ink-grey); }
  .card--dark .contact { top: 278px; color: var(--ink-soft); }

  .contact__item::after {
    content: "";
    display: inline-block;
    width: 9px;
    height: 9px;
    margin-left: 14px;
    background: var(--green);
    vertical-align: middle;
  }
</style>
</head>
<body>
<main class="sheet">

  <section class="card card--light" aria-label="Business card, light side">
    <div class="rule rule--top"></div>
    <div class="identity">
      <p class="identity__name">Calvin<br>Worthaven</p>
      <p class="identity__title">ARCHITECT</p>
    </div>
    <div class="rule rule--bottom"></div>
    <ul class="contact">
      <li class="contact__item">License No. 052816</li>
      <li class="contact__item">607 - 385 - 2194</li>
      <li class="contact__item">calvin@designbycw.com</li>
    </ul>
  </section>

  <section class="card card--dark" aria-label="Business card, grey side">
    <div class="identity">
      <p class="identity__name">Calvin<br>Worthaven</p>
      <p class="identity__title">ARCHITECT</p>
    </div>
    <ul class="contact">
      <li class="contact__item">License No. 052816</li>
      <li class="contact__item">607 - 385 - 2194</li>
      <li class="contact__item">calvin@designbycw.com</li>
    </ul>
  </section>

</main>
</body>
</html>
```